Marlow Vale Stud website

We would like to create a horse stud/agistment farm website similar to this websites we have attached below:
www.thornbeck.com.au
www.quillstead.com.au
www.brackley.com
www.pimsey.com.au
The main colour scheme are purple and white to align with the stable's racing colours.
We have also attach the company logo and also images of the farm and create some ideas for the website.
Many thanks for looking into this project!

```html
<!DOCTYPE html>
<html lang="en">
<head>
<meta charset="utf-8">
<title>Marlow Vale Stud</title>
<link href="https://fonts.googleapis.com/css2?family=Montserrat:wght@500;600;700;800&family=Open+Sans:wght@400;600;700&display=swap" rel="stylesheet">
<style>
:root{
  --purple:#4b1a50;
  --purple-deep:#2e0b33;
  --purple-mid:#6a2d6f;
  --footer:#3a0e3f;
  --footer-bar:#300a34;
  --ink:#2b2b2b;
  --muted:#6d6d6d;
  --white:#ffffff;
  --mist:#e9ecef;
}
*{margin:0;padding:0;box-sizing:border-box}
html,body{width:1200px;height:3607px;overflow:hidden;background:var(--white)}
body{position:relative;font-family:"Open Sans",Arial,sans-serif;color:var(--ink)}
.abs{position:absolute}
.heading{font-family:"Montserrat",Arial,sans-serif;font-weight:700;text-transform:uppercase}
.btn{position:absolute;display:flex;align-items:center;justify-content:center;font-family:"Montserrat",Arial,sans-serif;font-weight:700;font-size:16px;color:var(--white);background:var(--purple);text-transform:uppercase;letter-spacing:.3px}

/* header */
.site-header{left:0;top:0;width:1200px;height:96px;background:var(--white);z-index:5}
.brand{left:162px;top:30px;display:flex;align-items:center;gap:12px;font-family:"Montserrat",Arial,sans-serif;font-weight:700;font-size:24px;color:var(--purple-deep);text-transform:uppercase}
.brand-dot{width:26px;height:26px;border-radius:50%;background:var(--purple-deep)}
.main-nav{right:148px;top:38px;display:flex;gap:22px;font-family:"Montserrat",Arial,sans-serif;font-weight:600;font-size:15px;color:#222;text-transform:uppercase}

/* hero */
.hero{left:0;top:96px;width:1200px;height:614px;overflow:hidden}
.hero-photo{position:absolute;inset:0;background:linear-gradient(180deg,#5f8fc4 0%,#8fb3d9 30%,#6a5a48 55%,#3e3226 72%,#4b6a34 86%,#2f4a22 100%)}
.hero-title{left:0;width:1200px;top:212px;text-align:center;color:var(--white);line-height:1}
.hero-title .small{font-size:40px;font-weight:700;display:block}
.hero-title .big{font-size:58px;font-weight:700;display:block;margin-top:2px}
.hero-btn{left:493px;top:330px;width:192px;height:50px;border-radius:25px;background:var(--purple-deep)}
.dots{left:566px;top:520px;display:flex;gap:8px}
.dots span{width:13px;height:13px;border-radius:50%;border:2px solid var(--white)}
.dots span.on{background:var(--white)}

/* about */
.about-title{left:171px;top:788px;font-size:33px;color:var(--purple-deep)}
.about-text{left:171px;top:846px;width:400px;font-size:16px;line-height:28px;color:#555}
.about-btn{left:166px;top:1003px;width:174px;height:52px}
.video{left:606px;top:784px;width:448px;height:265px;background:linear-gradient(180deg,#7aa7d4 0%,#b9cfe2 22%,#6f8f5a 40%,#8aa56a 70%,#5a7a3e 100%)}
.play{left:799px;top:877px;width:64px;height:64px;border-radius:50%;background:var(--white)}

/* sale */
.sale{left:0;top:1106px;width:1200px;height:560px;background:linear-gradient(180deg,#f4f5f7 0%,#dde2e8 35%,#c9d0d8 60%,#e8eaee 100%)}
.section-mark{width:22px;height:22px;border-radius:50%;border:4px solid var(--purple-deep)}
.section-title{left:0;width:1200px;text-align:center;font-size:28px;color:var(--purple-deep)}
.horse-card{top:1270px;height:260px}
.card-a{left:156px;width:282px;background:linear-gradient(160deg,#3b3f4a,#8a8f98 45%,#5b3a3d 80%,#2d2d33)}
.card-b{left:459px;width:279px;background:linear-gradient(160deg,#5a4440,#7c6258 50%,#3c2d2c)}
.card-b .shade{position:absolute;inset:0;background:rgba(70,20,60,.62)}
.card-c{left:760px;width:279px;background:linear-gradient(160deg,#4f7d3e,#c9b792 45%,#e6d7b8 60%,#4a7b33)}
.card-label{left:0;width:100%;top:88px;text-align:center;color:var(--white)}
.card-label h3{font-family:"Montserrat",Arial,sans-serif;font-size:21px;font-weight:700;text-transform:uppercase}
.card-label p{font-size:14px;line-height:19px;width:200px;margin:8px auto 0}
.chev{left:123px;top:172px}
.arrow{top:1368px}

/* stallions */
.stallions{left:0;top:1600px;width:1200px;height:497px;background:linear-gradient(100deg,#7a3d80 0%,#5a2260 35%,#3d1144 65%,#24072a 100%)}
.stallion-photo{left:166px;top:1712px;width:459px;height:301px;background:linear-gradient(180deg,#3a2a30 0%,#5c3a40 30%,#6a7a6a 55%,#b0a89a 65%,#4c8a3c 80%,#d85a8a 92%,#3d6a2a 100%)}
.stallion-text{left:664px;top:1712px;width:380px;color:var(--white)}
.stallion-text h2{font-size:31px;line-height:36px}
.stallion-text h4{font-family:"Montserrat",Arial,sans-serif;font-size:18px;font-weight:700;text-transform:uppercase;margin-top:4px}
.stallion-text p{font-size:15px;line-height:26px;margin-top:16px;color:#efe4f0}
.stallion-btn{left:664px;top:1943px;width:168px;height:53px;background:#3d0f45}

/* news */
.news-card{top:2249px;width:274px;height:329px;background:var(--white);box-shadow:0 2px 10px rgba(0,0,0,.16)}
.news-img{position:absolute;left:11px;top:11px;width:252px;height:150px}
.img-1{background:linear-gradient(180deg,#b8cbe0 0%,#6f8e4a 30%,#7f9a5a 100%)}
.img-2{background:linear-gradient(180deg,#5a6a80 0%,#c8a878 35%,#4a5a3a 60%,#3f5a2c 100%)}
.img-3{background:linear-gradient(180deg,#9fb8d4 0%,#e8e0c8 30%,#3c5a2c 60%,#6a9a40 100%)}
.date{position:absolute;left:21px;top:116px;width:50px;height:56px;background:var(--purple-deep);color:var(--white);text-align:center;font-family:"Montserrat",Arial,sans-serif;font-weight:700;line-height:1}
.date b{display:block;font-size:22px;margin-top:8px}
.date span{display:block;font-size:12px;margin-top:3px}
.news-body{position:absolute;left:24px;top:184px;width:232px}
.news-body h3{font-size:14px;line-height:16px;font-weight:700;color:var(--purple-deep)}
.news-body p{font-size:11px;line-height:14px;color:#777;margin-top:10px}
.news-body .more{display:block;font-size:10px;font-weight:700;color:#222;margin-top:18px;text-transform:uppercase}

/* gallery */
.gallery{left:0;top:2633px;width:1200px;height:600px;background:linear-gradient(180deg,#ffffff 0%,#eef1f4 25%,#e3e8ec 55%,#dfe6dc 100%)}
.grass{left:0;top:2990px;width:1200px;height:240px;background:linear-gradient(180deg,#b8cf86 0%,#9dbb5a 35%,#7fa33e 70%,#5f8a2c 100%)}
.shot{position:absolute}
.shot-1{left:0;top:2797px;width:233px;height:238px;background:linear-gradient(180deg,#2f4a22,#4a6a2c 55%,#a07a4a 80%,#6a5a3a)}
.shot-2{left:240px;top:2833px;width:231px;height:236px;background:linear-gradient(180deg,#c8d4e0,#4a6a3a 45%,#6a8a4a 80%,#5a7a38)}
.shot-3{left:483px;top:2802px;width:229px;height:233px;background:linear-gradient(180deg,#6a98cc,#a8c4dc 20%,#5e8a38 45%,#7aa048 100%)}
.shot-4{left:724px;top:2833px;width:231px;height:236px;background:linear-gradient(180deg,#8aa6c2,#5a7a48 30%,#8a9a6a 60%,#6a8a4a)}
.shot-5{left:969px;top:2792px;width:231px;height:233px;background:linear-gradient(180deg,#4a84c8,#9ac0e0 30%,#6a9a40 55%,#4e8a2c)}

/* footer */
.site-footer{left:0;top:3210px;width:1200px;height:397px;background:var(--footer);color:var(--white)}
.footer-brand{left:150px;top:3280px;width:150px;font-family:"Montserrat",Arial,sans-serif;font-weight:700;font-size:20px;line-height:24px;text-transform:uppercase;color:var(--white)}
.foot-col{top:3270px}
.foot-col h4{font-family:"Montserrat",Arial,sans-serif;font-size:17px;font-weight:700;text-transform:uppercase;margin-bottom:8px}
.foot-col li{list-style:none;font-size:14px;line-height:26.5px;color:#c9b8cc}
.socials{left:884px;top:3306px;display:flex;gap:8px}
.socials span{width:36px;height:36px;border-radius:50%;border:2px solid var(--white)}
.foot-bar{left:0;top:3530px;width:1200px;height:77px;background:var(--footer-bar);border-top:1px solid #5a2a5e;text-align:center;font-size:14px;line-height:60px;color:#b9a6bd}
</style>
</head>
<body>

<header class="site-header abs">
  <div class="brand abs"><span class="brand-dot"></span>Marlow Vale Stud.</div>
  <nav class="main-nav abs"><span>About</span><span>News</span><span>Gallery</span><span>Video</span><span>Stallions</span><span>Sales</span><span>Contact</span></nav>
</header>

<section class="hero abs">
  <div class="hero-photo" role="img" aria-label="Horses standing in a paddock under a blue sky, seen from below"></div>
  <h1 class="hero-title abs heading"><span class="small">Welcome to</span><span class="big">Marlow Vale Stud</span></h1>
  <div class="btn hero-btn">Read more</div>
  <div class="dots abs"><span></span><span class="on"></span><span></span></div>
  <svg class="abs" style="left:0;bottom:0" width="1200" height="50" viewBox="0 0 1200 50"><path d="M0 22 L40 30 L70 24 L110 34 L150 28 L200 36 L240 26 L290 32 L330 24 L380 34 L420 30 L470 38 L520 28 L560 34 L610 26 L660 36 L700 30 L750 38 L800 28 L850 34 L900 26 L950 32 L1000 24 L1050 34 L1100 28 L1150 36 L1200 26 L1200 50 L0 50Z" fill="#fff"/></svg>
</section>

<h2 class="about-title abs heading">Marlow Vale Stud</h2>
<p class="about-text abs">Pellentesque faucibus Ut accumsan ultricies elit Maecenas at justo id velit placerat molestie Donec dictum lectus non odio Cras a ante vitae enim iaculis aliquam Mauris nunc quam venenatis nec euismod sit amet egestas placerat est</p>
<div class="btn about-btn">Read more</div>
<div class="video abs" role="img" aria-label="Aerial view of the farm stables and green paddocks"></div>
<div class="play abs"></div>
<svg class="abs" style="left:820px;top:894px" width="26" height="30" viewBox="0 0 26 30"><path d="M2 0 L26 15 L2 30Z" fill="#2a2a2a"/></svg>

<section class="sale abs" role="img" aria-label="Misty mountain range background"></section>
<div class="section-mark abs" style="left:589px;top:1150px"></div>
<h2 class="section-title abs heading" style="top:1200px">Horse for sale</h2>
<div class="horse-card card-a abs" role="img" aria-label="Grey racehorse with handlers after a race"></div>
<div class="horse-card card-b abs" role="img" aria-label="Horse for sale">
  <div class="shade"></div>
  <div class="card-label abs"><h3>Horse title</h3><p>Lorem ipsum dolor sit amet consectetur adipiscing</p></div>
  <svg class="chev abs" width="34" height="34" viewBox="0 0 34 34"><circle cx="17" cy="17" r="15" fill="none" stroke="#fff" stroke-width="2"/><path d="M10 14 L17 21 L24 14" fill="none" stroke="#fff" stroke-width="2.5"/></svg>
</div>
<div class="horse-card card-c abs" role="img" aria-label="Palomino horse in a green paddock"></div>
<svg class="arrow abs" style="left:120px" width="20" height="34" viewBox="0 0 20 34"><path d="M17 3 L4 17 L17 31" fill="none" stroke="#555" stroke-width="3"/></svg>
<svg class="arrow abs" style="left:1055px" width="20" height="34" viewBox="0 0 20 34"><path d="M3 3 L16 17 L3 31" fill="none" stroke="#555" stroke-width="3"/></svg>

<section class="stallions abs"></section>
<svg class="abs" style="left:0;top:1590px" width="1200" height="70" viewBox="0 0 1200 70"><path d="M0 0 L1200 0 L1200 16 L1150 22 L1120 12 L1080 20 L1030 14 L990 26 L940 18 L900 30 L850 20 L800 34 L760 26 L700 38 L650 30 L600 44 L540 36 L480 50 L420 40 L360 54 L300 44 L240 58 L180 48 L120 62 L60 52 L0 60Z" fill="#e3e7ec"/></svg>
<div class="stallion-photo abs" role="img" aria-label="Jockey in purple silks riding a grey horse at a night race"></div>
<div class="stallion-text abs">
  <h2 class="heading">Stallions</h2>
  <h4>Amet consectetuer adipiscing</h4>
  <p>Pellentesque faucibus Ut accumsan ultricies elit Maecenas at justo id velit placerat molestie Donec dictum lectus non odio Cras a ante vitae enim iaculis aliquam Mauris nunc quam venenatis nec euismod sit amet egestas placerat est</p>
</div>
<div class="btn stallion-btn">Read more</div>

<div class="section-mark abs" style="left:585px;top:2140px"></div>
<h2 class="section-title abs heading" style="top:2181px">Latest news</h2>

<article class="news-card abs" style="left:159px">
  <div class="news-img img-1" role="img" aria-label="Paddocks with fenced runs"></div>
  <div class="date"><b>31</b><span>JAN</span></div>
  <div class="news-body"><h3>Duis non nunc Nulla rhoncus dictum metus Curabitur</h3><p>Duis non nunc Nulla rhoncus dictum metus Curabitur tristique mi condimentum orci Phasellus pellentesq.</p><span class="more">Read more</span></div>
</article>
<article class="news-card abs" style="left:464px">
  <div class="news-img img-2" role="img" aria-label="Sunset over farm fields"></div>
  <div class="date"><b>20</b><span>JAN</span></div>
  <div class="news-body"><h3>Duis non nunc Nulla rhoncus dictum metus Curabitur</h3><p>Duis non nunc Nulla rhoncus dictum metus Curabitur tristique mi condimentum orci Phasellus pellentesq.</p><span class="more">Read more</span></div>
</article>
<article class="news-card abs" style="left:767px">
  <div class="news-img img-3" role="img" aria-label="Sunlit pasture with trees"></div>
  <div class="date"><b>14</b><span>JAN</span></div>
  <div class="news-body"><h3>Duis non nunc Nulla rhoncus dictum metus Curabitur</h3><p>Duis non nunc Nulla rhoncus dictum metus Curabitur tristique mi condimentum orci Phasellus pellentesq.</p><span class="more">Read more</span></div>
</article>

<section class="gallery abs" role="img" aria-label="Cloudy sky and treeline"></section>
<div class="section-mark abs" style="left:594px;top:2686px"></div>
<h2 class="section-title abs heading" style="top:2727px">Our gallery</h2>
<div class="grass abs" role="img" aria-label="Long green grass in the foreground"></div>
<div class="shot shot-1" role="img" aria-label="Tree-lined dirt lane"></div>
<div class="shot shot-2" role="img" aria-label="Horses grazing under trees"></div>
<div class="shot shot-3" role="img" aria-label="Green crop field"></div>
<div class="shot shot-4" role="img" aria-label="Aerial view of stables"></div>
<div class="shot shot-5" role="img" aria-label="Open paddock under blue sky"></div>

<footer class="site-footer abs"></footer>
<svg class="abs" style="left:0;top:3180px" width="1200" height="60" viewBox="0 0 1200 60"><path d="M0 34 L50 26 L90 36 L140 24 L190 34 L240 28 L290 38 L340 26 L390 36 L440 22 L490 34 L540 28 L590 38 L640 24 L690 34 L740 28 L790 38 L840 26 L890 36 L940 24 L990 34 L1040 28 L1090 38 L1140 26 L1200 34 L1200 60 L0 60Z" fill="#3a0e3f"/></svg>
<div class="footer-brand abs">Marlow Vale Stud</div>
<div class="foot-col abs" style="left:354px"><h4>Contact us</h4><ul><li>42 Alder Lane #4B</li><li>Kent 20418 KT</li><li>555.014.2290</li><li>info@marlowvale.com</li></ul></div>
<div class="foot-col abs" style="left:572px"><h4>Quick links</h4><ul><li>Artist</li><li>Sales</li><li>Stallion</li><li>Gallery</li><li>Videos</li></ul></div>
<div class="foot-col abs" style="left:729px"><h4>Resources</h4><ul><li>Blogs</li><li>News</li><li>Our Horses</li><li>Sales</li><li>Contact</li></ul></div>
<div class="foot-col abs" style="left:883px"><h4>Get in touch</h4></div>
<div class="socials abs"><span></span><span></span><span></span><span></span></div>
<div class="foot-bar abs">Copyright © 2019 All right reserved</div>

</body>
</html>
```